Business Card design for insurance broker in Denver, CO, USA

I need a business card designed using this logo that was just created. We sell life and disability income insurance to US consumers.
Looking for a professionally designed card to make use of the logo and have something to hand to prospects or new business referral sources. The card could be white, gray, black or whatever you would recommend.

Target Market(s)

US Consumers and other financial professionals that I partner with.

Industry/Entity Type

Insurance Broker

Contact Information for Business Card

Owen T. Farrow, CLU, LUTCF (please note that CLU should have a superscript R in a circle for registered trademark)
President
phone (303) 555-0187
email owen@keelbrookcover.example
4620 W. Halvern Rd, Suite 300, Greenwood Village, CO 80111
Somewhere fit in a tagline saying "Your resource for life, long term care, and disability insurance" (maybe the back if it doesn't fit on the front, your call)

Font styles to use
Sans Serif

Requirements
Must have
• Must have logo in correct blue and gray colors, my name, address, phone, email. Order and placement determined by the designer.
• I just want something that looks a more professional than what I could have done using the business card designer tool on pixelbazaar.example or QuillPress, or any other do-it-yourself tool
• A regular rectangular business card with square corners is preferred
Nice to have
• I included the logos of 2 organizations I belong to (GKLS and WOBCE). They should be small, but visible on the back only. If it doesn’t look good, this is not a requirement, feel free to drop it.
Should not have
• Do not add any colors not already in the logo, except use of black and whites which are okay. If you use the logo on the back and want to make that in all black, gray or white, that may be okay as well.

```html
<!DOCTYPE html>
<html lang="en">
<head>
<meta charset="utf-8">
<title>Keelbrook Cover — Business Card</title>
<link rel="stylesheet" href="https://fonts.googleapis.com/css2?family=Lato:wght@400;700&family=Libre+Baskerville&display=swap">
<style>
  :root {
    --backdrop: #e4e5e9;
    --card: #ffffff;
    --brand-blue: #1f86d1;
    --text-gray: #8c8c8c;
    --label-gray: #9a9a9a;
    --tone-light: #c4c4c4;
    --tone-mid: #8e8e8e;
    --tone-dark: #4a4a4a;
  }
  * { box-sizing: border-box; margin: 0; padding: 0; }
  html, body { width: 1200px; height: 1200px; overflow: hidden; }
  body { background: var(--backdrop); font-family: "Lato", sans-serif; position: relative; }

  .card {
    position: absolute;
    left: 264px;
    width: 672px;
    height: 437px;
    background: var(--card);
    overflow: hidden;
  }
  .card--front { top: 121px; }
  .card--back { top: 641px; }
  .card__panel { position: absolute; inset: 0; width: 100%; height: 100%; }

  .brand {
    position: absolute;
    color: var(--brand-blue);
    font-weight: 700;
    text-transform: uppercase;
  }
  .brand--front { left: 65px; top: 186px; font-size: 31px; line-height: 1.08; letter-spacing: 0.5px; }
  .brand--back { left: 222px; right: 0; top: 91px; text-align: center; font-size: 13px; letter-spacing: 1.5px; }

  .identity { position: absolute; left: 222px; right: 0; text-align: center; }
  .identity__title { top: 149px; color: var(--label-gray); font-weight: 700; font-size: 13px; letter-spacing: 3.5px; }
  .identity__name { top: 175px; color: var(--brand-blue); font-family: "Libre Baskerville", serif; font-size: 21px; letter-spacing: 3px; }
  .identity__creds { top: 205px; color: var(--label-gray); font-weight: 700; font-size: 13px; letter-spacing: 2.5px; }
  .identity__creds sup { font-size: 8px; letter-spacing: 0; }

  .contact { position: absolute; left: 326px; top: 252px; list-style: none; color: var(--text-gray); font-size: 13px; letter-spacing: 1.6px; line-height: 22px; }
  .contact__item { display: flex; align-items: flex-start; gap: 14px; margin-bottom: 14px; }
  .contact__icon { width: 15px; height: 15px; margin-top: 3px; fill: var(--brand-blue); flex: none; }
</style>
</head>
<body>

<section class="card card--front" aria-label="Card front">
  <svg class="card__panel" viewBox="0 0 583 379" preserveAspectRatio="none" role="img" aria-label="Grey geometric decorative panel">
    <defs>
      <linearGradient id="panel-tone-front" x1="0" y1="0" x2="1" y2="0">
        <stop offset="0" stop-color="var(--tone-light)"/>
        <stop offset="0.55" stop-color="var(--tone-mid)"/>
        <stop offset="1" stop-color="var(--tone-dark)"/>
      </linearGradient>
    </defs>
    <polygon fill="url(#panel-tone-front)" points="216,0 583,0 583,379 216,379 404,190"/>
  </svg>
  <div class="brand brand--front">Keelbrook<br>Cover</div>
</section>

<section class="card card--back" aria-label="Card back">
  <svg class="card__panel" viewBox="0 0 583 379" preserveAspectRatio="none" role="img" aria-label="Grey geometric decorative panel">
    <defs>
      <linearGradient id="panel-tone-back" x1="1" y1="0" x2="0" y2="0">
        <stop offset="0" stop-color="var(--tone-light)"/>
        <stop offset="0.55" stop-color="var(--tone-mid)"/>
        <stop offset="1" stop-color="var(--tone-dark)"/>
      </linearGradient>
    </defs>
    <polygon fill="url(#panel-tone-back)" points="0,0 291,0 104,190 291,379 0,379"/>
  </svg>

  <div class="brand brand--back">Keelbrook Cover</div>

  <p class="identity identity__title">PRESIDENT</p>
  <p class="identity identity__name">OWEN T. FARROW</p>
  <p class="identity identity__creds">CLU<sup>®</sup>, LUTCF</p>

  <ul class="contact">
    <li class="contact__item">
      <svg class="contact__icon" viewBox="0 0 16 16" aria-hidden="true"><path d="M11.5 1.5l2.5 2.3c.4.4.4 1 0 1.4l-1.5 1.3c-.9-1-2-1.8-3.3-2.1zM3.5 14.5C2 13 1.8 10.5 3 8.6c1-1.6 2.6-2.9 4.4-3.4l.8 1.4c-1.3.6-2.4 1.6-3.1 2.9-.6 1.2-.6 2.5.1 3.6z"/></svg>
      <span>(303) 555-0187</span>
    </li>
    <li class="contact__item">
      <svg class="contact__icon" viewBox="0 0 16 16" aria-hidden="true"><path d="M1 4h14v9H1z"/><path d="M1 4l7 5 7-5" fill="none" stroke="#fff" stroke-width="1.3"/></svg>
      <span>owen@keelbrookcover.example</span>
    </li>
    <li class="contact__item">
      <svg class="contact__icon" viewBox="0 0 16 16" aria-hidden="true"><path d="M8 0.5a5.5 5.5 0 0 0-5.5 5.5c0 4 5.5 9.5 5.5 9.5s5.5-5.5 5.5-9.5A5.5 5.5 0 0 0 8 0.5zm0 7.6a2.1 2.1 0 1 1 0-4.2 2.1 2.1 0 0 1 0 4.2z"/></svg>
      <span>4620 W. Halvern Rd, Suite 300,<br>Larkmoor Springs, CO 80954</span>
    </li>
  </ul>
</section>

</body>
</html>
```